TL - business card

Tallow Partners is an insurance brokerage firm, inovative, proactive, vigorous, which aims to become the leader of the insurance brokers in Anfrica. We should like to get some designs which should be avoided also in Gray / Metallic for the Administration and Orange / Blue for the Managers (ike in the picture sent). The Blue / Green logo is not the correct one, but the source of the file. Please adjust the color accordingly for the business cards. 1 / Orange / Blue 2 / Gray / Metallic We want something classic but which is transmitted strenght, inovation, modernity and most of all, rapidity. We want something start-up like, very punchy and catching eye remaining profesional at the same time. Name: Dorian Whitlock Function: Managing Director Address: N ° 17/18 Rua Veloso - R / C 2B Direita - Bairro Mutamba - Luanda Tel: (+244) 947 582 316 Email: dorian.whitlock@tallow-p.example Website: www.tallow-p. example We want classic in the front and creative, colorfull at the back. The cards will be printed in relief, with very high quality of paper.
Insurance Broker
Colors
Designer to choose colors to be used in the design.

```html
<!DOCTYPE html>
<html lang="en">
<head>
<meta charset="utf-8">
<title>Tallow Partners – Business Card</title>
<link rel="stylesheet" href="https://fonts.googleapis.com/css2?family=Montserrat:wght@400;500;600&display=swap">
<style>
  :root {
    --stage: #ecebe8;
    --card: #1d1d1e;
    --card-edge: #161617;
    --brand-blue: #29a3df;
    --text-light: #e8e8e8;
    --text-muted: #bdbdbd;
  }
  * { margin: 0; padding: 0; box-sizing: border-box; }
  html, body {
    width: 1200px; height: 912px; overflow: hidden;
    background: var(--stage);
    font-family: "Montserrat", Arial, sans-serif;
  }
  .canvas {
    position: relative; width: 1200px; height: 912px;
  }
  .card {
    position: absolute; left: 320px;
    width: 560px; height: 320px;
    background: var(--card);
    border-radius: 18px;
    box-shadow: 0 10px 28px rgba(0,0,0,.25);
    overflow: hidden;
  }
  .card--front { top: 110px; }
  .card--back { top: 482px; }

  /* front */
  .brand {
    position: absolute; inset: 0;
    display: flex; align-items: center; justify-content: center; gap: 14px;
  }
  .brand__dot {
    width: 22px; height: 22px; border-radius: 50%;
    background: var(--brand-blue);
  }
  .brand__name {
    font-weight: 600; font-size: 34px; letter-spacing: 1px;
    color: var(--brand-blue); text-transform: uppercase;
  }

  /* back */
  .identity {
    position: absolute; left: 40px; top: 150px; width: 250px;
    text-align: right;
  }
  .identity__name {
    font-weight: 500; font-size: 22px; letter-spacing: 2px;
    color: var(--brand-blue); text-transform: uppercase; white-space: nowrap;
  }
  .identity__role {
    margin-top: 2px; font-size: 13px; color: var(--text-light);
  }
  .divider {
    position: absolute; left: 312px; top: 112px;
    width: 1.5px; height: 96px; background: var(--brand-blue);
  }
  .contact {
    position: absolute; left: 330px; top: 108px;
    font-size: 11.5px; line-height: 18px; color: var(--text-muted);
    list-style: none;
  }
  .contact__row { display: flex; align-items: center; gap: 8px; white-space: nowrap; }
  .contact__row--icon { padding-left: 0; }
  .contact__text--indent { padding-left: 0; }
  .contact__icon { width: 11px; height: 11px; flex: none; }
</style>
</head>
<body>
<main class="canvas">
  <section class="card card--front" aria-label="Card front">
    <div class="brand">
      <span class="brand__dot"></span>
      <span class="brand__name">Tallow Partners</span>
    </div>
  </section>

  <section class="card card--back" aria-label="Card back">
    <div class="identity">
      <p class="identity__name">Dorian Whitlock</p>
      <p class="identity__role">Managing Director</p>
    </div>
    <span class="divider"></span>
    <ul class="contact">
      <li class="contact__row">N° 17/18 Rua Veloso</li>
      <li class="contact__row">R / C 2B Direita</li>
      <li class="contact__row">Bairro Mutamba - Luanda</li>
      <li class="contact__row">
        <svg class="contact__icon" viewBox="0 0 24 24" aria-hidden="true">
          <path fill="#29a3df" d="M6.6 10.8a15.1 15.1 0 0 0 6.6 6.6l2.2-2.2c.3-.3.7-.4 1-.2 1.1.4 2.3.6 3.6.6.6 0 1 .4 1 1V20c0 .6-.4 1-1 1A17 17 0 0 1 3 4c0-.6.4-1 1-1h3.5c.6 0 1 .4 1 1 0 1.3.2 2.5.6 3.6.1.3 0 .7-.2 1z"/>
        </svg>
        (+244) 947 582 316
      </li>
      <li class="contact__row">
        <svg class="contact__icon" viewBox="0 0 24 24" aria-hidden="true">
          <rect x="2.5" y="5" width="19" height="14" rx="1.5" fill="none" stroke="#29a3df" stroke-width="2"/>
          <path d="M3 6l9 7 9-7" fill="none" stroke="#29a3df" stroke-width="2"/>
        </svg>
        dorian.whitlock@tallow-p.example
      </li>
    </ul>
  </section>
</main>
</body>
</html>
```